PowerPoint template design for TJMalverne Consulting

I'm interested in a PowerPoint template design that incorporates my logo (see attached file). I am an economist who mostly shows charts and tables in Calibri 24 point. Most tables are 4 or 5 columns by 14 or 15 rows so the design should seek to maximize work space on the slide while unmistakably indicating that these are my slides. I will be using the template design when I provide copies of my slides to the audience after the presentation, mostly in PDF format.

Target Market(s)

Mostly non-data types including educators.

Industry/Entity Type

Consulting

Font styles to use
Sans Serif

Colors
00a990
33b8a4
86cfc6

Requirements
Must have
• Looking for something more sleek and subtle, that doesn't take up too much screen real estate and that in some manner incorporates my business card/logo design. The logo doesn't have to be exactly incorporated as is, but it should visually align or mesh. I like the teal and gray/dark gray color palette that is on my business card.
Nice to have
• Open to more transparency/faded coloring, less bold and vivid than subtle background.
Should not have
• The goal is a PP template design that is unmistakably mine but is not so intrusive that it is the focus of every slide. I want the viewer to forget that the slide is coming from me as a consultant and focus on the content of the slide. I'm not using this as part of a marketing or advertising push as much as I am marking my material so folks who refer to the slides at a later date will know that they are mine.

```html
<!DOCTYPE html>
<html lang="en">
<head>
<meta charset="utf-8">
<title>TJMalverne Consulting – Slide Template</title>
<link href="https://fonts.googleapis.com/css2?family=Carlito:wght@400;700&display=swap" rel="stylesheet">
<style>
:root{
  --teal:#00a990;
  --teal-mid:#33b8a4;
  --teal-light:#86cfc6;
  --ink:#3c3f42;
  --grey:#8a8d90;
  --grey-light:#d9dadb;
  --page:#e6e6e6;
  --navy:#3b5f8c;
  --white:#ffffff;
}
*{box-sizing:border-box;margin:0;padding:0}
html,body{width:849px;height:1200px;overflow:hidden;background:var(--page);font-family:"Carlito",Calibri,sans-serif;color:var(--ink)}
.slide{position:absolute;left:118px;width:612px;height:545px;background:var(--white);box-shadow:0 2px 6px rgba(0,0,0,.25);overflow:hidden}
.slide--chart{top:14px}
.slide--programme{top:574px}
.slide-header{position:absolute;left:0;top:14px;height:34px;padding-left:22px;border-left:6px solid var(--teal)}
.slide-header .tagline{font-size:10.5px;font-weight:700;letter-spacing:.2px;color:var(--ink)}
.slide-header .date{font-size:9.5px;color:var(--teal);margin-top:3px}
.header-rule{position:absolute;left:28px;right:28px;top:52px;height:1px;background:var(--grey-light)}
.slide-title{position:absolute;left:28px;top:62px;font-size:22px;font-weight:700;color:var(--teal);letter-spacing:.3px}
.slide-footer{position:absolute;left:0;right:0;bottom:0;height:44px}
.footer-band{position:absolute;left:0;right:150px;bottom:14px;height:3px;background:linear-gradient(90deg,rgba(0,169,144,.15),var(--teal-light) 60%,var(--teal))}
.brand{position:absolute;right:14px;bottom:6px;display:flex;align-items:center;gap:6px;padding:4px 8px;background:var(--white)}
.brand-square{width:16px;height:16px;background:var(--teal)}
.brand-name{font-size:12px;font-weight:700;color:var(--ink);white-space:nowrap}

/* chart */
.chart{position:absolute;left:34px;top:100px;width:548px}
.plot-wrap{position:relative;margin-left:60px;height:200px}
.y-axis{position:absolute;left:-22px;top:0;height:100%;width:18px}
.y-axis span{position:absolute;right:0;font-size:7px;color:var(--grey);transform:translateY(-50%)}
.plot{display:flex;height:100%;border-left:1px solid var(--grey);border-bottom:1px solid var(--grey);
  background-image:linear-gradient(var(--grey-light) 1px,transparent 1px);background-size:100% calc(100% / 7)}
.group{flex:1;display:flex;align-items:flex-end;justify-content:center;gap:1px}
.bar{width:5px;height:calc(var(--v) / 35 * 100%)}
.s1{background:var(--navy)}
.s2{background:var(--teal)}
.s3{background:var(--grey)}
.s4{background:var(--teal-mid)}
.s5{background:var(--teal-light)}
.data-table{width:548px;border-collapse:collapse;table-layout:fixed;font-size:6.3px;color:var(--ink)}
.data-table th,.data-table td{border:1px solid var(--grey-light);text-align:center;padding:1px 0;height:14px}
.data-table thead th{font-weight:400;height:30px;line-height:1.1}
.data-table .series{width:60px;text-align:left;padding-left:3px;white-space:nowrap}
.key{display:inline-block;width:5px;height:5px;margin-right:3px;vertical-align:middle}

/* programme */
.programme{position:absolute;left:0;top:96px}
.stage{position:absolute;width:150px}
.stage-name{font-size:11.5px;font-weight:700;color:var(--ink)}
.stage ul{list-style:none;margin-top:2px}
.stage li{font-size:9.5px;color:var(--ink);padding-left:10px;position:relative;line-height:1.3}
.stage li::before{content:"";position:absolute;left:2px;top:5px;width:4px;height:4px;border-radius:50%;background:var(--teal)}
.stage--right{text-align:left}
</style>
</head>
<body>

<section class="slide slide--chart">
  <header class="slide-header">
    <p class="tagline">LABOR MARKET ECONOMIST AND SPEAKER PAR EXCELLENCE</p>
    <p class="date">July 2015</p>
  </header>
  <div class="header-rule"></div>
  <h1 class="slide-title">OUR CHART</h1>

  <div class="chart">
    <div class="plot-wrap">
      <div class="y-axis">
        <span style="top:0%">35</span><span style="top:14.29%">30</span><span style="top:28.57%">25</span><span style="top:42.86%">20</span>
        <span style="top:57.14%">15</span><span style="top:71.43%">10</span><span style="top:85.71%">5</span><span style="top:100%">0</span>
      </div>
      <div class="plot" role="img" aria-label="Bar chart of growth rates by region over five periods">
        <div class="group"><i class="bar s1" style="--v:8"></i><i class="bar s2" style="--v:15.6"></i><i class="bar s3" style="--v:4.8"></i><i class="bar s4" style="--v:13.2"></i><i class="bar s5" style="--v:3.2"></i></div>
        <div class="group"><i class="bar s1" style="--v:11.4"></i><i class="bar s2" style="--v:11.5"></i><i class="bar s3" style="--v:4.8"></i><i class="bar s4" style="--v:10.8"></i><i class="bar s5" style="--v:6.8"></i></div>
        <div class="group"><i class="bar s1" style="--v:5"></i><i class="bar s2" style="--v:5.2"></i><i class="bar s3" style="--v:3"></i><i class="bar s4" style="--v:6.1"></i><i class="bar s5" style="--v:3.8"></i></div>
        <div class="group"><i class="bar s1" style="--v:14.8"></i><i class="bar s2" style="--v:17.1"></i><i class="bar s3" style="--v:10.7"></i><i class="bar s4" style="--v:16.4"></i><i class="bar s5" style="--v:10.7"></i></div>
        <div class="group"><i class="bar s1" style="--v:1.8"></i><i class="bar s2" style="--v:4.8"></i><i class="bar s3" style="--v:1.1"></i><i class="bar s4" style="--v:5.3"></i><i class="bar s5" style="--v:1.1"></i></div>
        <div class="group"><i class="bar s1" style="--v:16.1"></i><i class="bar s2" style="--v:30.6"></i><i class="bar s3" style="--v:10"></i><i class="bar s4" style="--v:28.9"></i><i class="bar s5" style="--v:10"></i></div>
        <div class="group"><i class="bar s1" style="--v:9.6"></i><i class="bar s2" style="--v:15.8"></i><i class="bar s3" style="--v:6.4"></i><i class="bar s4" style="--v:14.6"></i><i class="bar s5" style="--v:5.4"></i></div>
        <div class="group"><i class="bar s1" style="--v:8.7"></i><i class="bar s2" style="--v:14.8"></i><i class="bar s3" style="--v:5.4"></i><i class="bar s4" style="--v:13.5"></i><i class="bar s5" style="--v:5.4"></i></div>
        <div class="group"><i class="bar s1" style="--v:11.9"></i><i class="bar s2" style="--v:15.6"></i><i class="bar s3" style="--v:4.9"></i><i class="bar s4" style="--v:14.1"></i><i class="bar s5" style="--v:3.9"></i></div>
        <div class="group"><i class="bar s1" style="--v:5.3"></i><i class="bar s2" style="--v:11.1"></i><i class="bar s3" style="--v:4.9"></i><i class="bar s4" style="--v:10.2"></i><i class="bar s5" style="--v:6.5"></i></div>
        <div class="group"><i class="bar s1" style="--v:14.2"></i><i class="bar s2" style="--v:5.2"></i><i class="bar s3" style="--v:3.1"></i><i class="bar s4" style="--v:6"></i><i class="bar s5" style="--v:3.5"></i></div>
        <div class="group"><i class="bar s1" style="--v:2"></i><i class="bar s2" style="--v:17.1"></i><i class="bar s3" style="--v:10.7"></i><i class="bar s4" style="--v:16.8"></i><i class="bar s5" style="--v:9.9"></i></div>
        <div class="group"><i class="bar s1" style="--v:15.8"></i><i class="bar s2" style="--v:30.5"></i><i class="bar s3" style="--v:10.1"></i><i class="bar s4" style="--v:29.4"></i><i class="bar s5" style="--v:9.7"></i></div>
        <div class="group"><i class="bar s1" style="--v:9.4"></i><i class="bar s2" style="--v:15.4"></i><i class="bar s3" style="--v:6.2"></i><i class="bar s4" style="--v:14.8"></i><i class="bar s5" style="--v:5.1"></i></div>
      </div>
    </div>
    <table class="data-table">
      <thead>
        <tr><th class="series"></th><th>North America</th><th>Latin America</th><th>Western Europe</th><th>Eastern Europe</th><th>Asia Pacific</th><th>Middle East, Africa</th><th>Global</th><th>North America</th><th>Latin America</th><th>Western Europe</th><th>Japan</th><th>Asia Pacific</th><th>Middle East, Africa</th><th>Global</th></tr>
      </thead>
      <tbody>
        <tr><td class="series"><i class="key s1"></i>2002–2006</td><td>8.0</td><td>11.4</td><td>5.0</td><td>14.8</td><td>1.8</td><td>16.1</td><td>9.6</td><td>8.7</td><td>11.9</td><td>5.3</td><td>14.2</td><td>2.0</td><td>15.8</td><td>9.4</td></tr>
        <tr><td class="series"><i class="key s2"></i>2007–2009</td><td>15.6</td><td>11.5</td><td>5.2</td><td>17.1</td><td>4.8</td><td>30.6</td><td>15.8</td><td>14.8</td><td>15.6</td><td>11.1</td><td>5.2</td><td>17.1</td><td>30.5</td><td>15.4</td></tr>
        <tr><td class="series"><i class="key s3"></i>2008–2010</td><td>4.8</td><td>4.8</td><td>3.0</td><td>10.7</td><td>1.1</td><td>10.0</td><td>6.4</td><td>5.4</td><td>4.9</td><td>4.9</td><td>3.1</td><td>10.7</td><td>10.1</td><td>6.2</td></tr>
        <tr><td class="series"><i class="key s4"></i>2011–2015</td><td>13.2</td><td>10.8</td><td>6.1</td><td>16.4</td><td>5.3</td><td>28.9</td><td>14.6</td><td>13.5</td><td>14.1</td><td>10.2</td><td>6.0</td><td>16.8</td><td>29.4</td><td>14.8</td></tr>
        <tr><td class="series"><i class="key s5"></i>2014–2016</td><td>3.2</td><td>6.8</td><td>3.8</td><td>10.7</td><td>1.1</td><td>10.0</td><td>5.4</td><td>5.4</td><td>3.9</td><td>6.5</td><td>3.5</td><td>9.9</td><td>9.7</td><td>5.1</td></tr>
      </tbody>
    </table>
  </div>

  <footer class="slide-footer">
    <div class="footer-band"></div>
    <div class="brand"><span class="brand-square"></span><span class="brand-name">TJMalverne Consulting</span></div>
  </footer>
</section>

<section class="slide slide--programme">
  <header class="slide-header">
    <p class="tagline">LABOR MARKET ECONOMIST AND SPEAKER PAR EXCELLENCE</p>
    <p class="date">July 2015</p>
  </header>
  <div class="header-rule"></div>
  <h1 class="slide-title">OUR PROGRAMME</h1>

  <svg class="programme" width="612" height="400" viewBox="0 0 612 400" aria-label="Eight stage programme cycle">
    <defs>
      <marker id="arrowhead" viewBox="0 0 10 10" refX="9" refY="5" markerWidth="6" markerHeight="6" orient="auto">
        <path d="M0 0 L10 5 L0 10 z" fill="var(--ink)"/>
      </marker>
    </defs>
    <g stroke="var(--ink)" stroke-width="1.2" fill="none" marker-end="url(#arrowhead)">
      <path d="M250 130 L200 40 L170 40"/>
      <path d="M230 180 L170 145"/>
      <path d="M230 225 L170 250"/>
      <path d="M250 275 L200 350 L170 350"/>
      <path d="M362 130 L412 40 L442 40"/>
      <path d="M382 180 L442 145"/>
      <path d="M382 225 L442 250"/>
      <path d="M362 275 L412 350 L442 350"/>
    </g>
    <g transform="translate(306 202)">
      <circle r="77.5" fill="none" stroke="var(--teal)" stroke-width="36" stroke-dasharray="56 4.87" stroke-dashoffset="-2.43" transform="rotate(-112.5)"/>
      <circle r="52" fill="var(--white)" stroke="var(--teal)" stroke-width="2"/>
      <g fill="var(--white)" font-size="14" font-weight="700" text-anchor="middle" dominant-baseline="central">
        <text x="0" y="-77.5">01</text>
        <text x="54.8" y="-54.8">02</text>
        <text x="77.5" y="0">03</text>
        <text x="54.8" y="54.8">04</text>
        <text x="0" y="77.5">05</text>
        <text x="-54.8" y="54.8">06</text>
        <text x="-77.5" y="0">07</text>
        <text x="-54.8" y="-54.8">08</text>
      </g>
      <text fill="var(--ink)" font-size="13" font-weight="700" text-anchor="middle"><tspan x="0" y="-3">YOUR TEXT</tspan><tspan x="0" y="13">HERE</tspan></text>
    </g>
  </svg>

  <div class="stage" style="left:28px;top:114px"><p class="stage-name">Stage name comes here</p><ul><li>Your text here</li><li>Your text here</li><li>Your text here</li></ul></div>
  <div class="stage" style="left:28px;top:222px"><p class="stage-name">Stage name comes here</p><ul><li>Your text here</li><li>Your text here</li><li>Your text here</li></ul></div>
  <div class="stage" style="left:28px;top:326px"><p class="stage-name">Stage name comes here</p><ul><li>Your text here</li><li>Your text here</li><li>Your text here</li></ul></div>
  <div class="stage" style="left:28px;top:428px"><p class="stage-name">Stage name comes here</p><ul><li>Your text here</li><li>Your text here</li><li>Your text here</li></ul></div>
  <div class="stage stage--right" style="left:450px;top:114px"><p class="stage-name">Stage name comes here</p><ul><li>Your text here</li><li>Your text here</li><li>Your text here</li></ul></div>
  <div class="stage stage--right" style="left:450px;top:222px"><p class="stage-name">Stage name comes here</p><ul><li>Your text here</li><li>Your text here</li><li>Your text here</li></ul></div>
  <div class="stage stage--right" style="left:450px;top:326px"><p class="stage-name">Stage name comes here</p><ul><li>Your text here</li><li>Your text here</li><li>Your text here</li></ul></div>
  <div class="stage stage--right" style="left:450px;top:428px"><p class="stage-name">Stage name comes here</p><ul><li>Your text here</li><li>Your text here</li><li>Your text here</li></ul></div>

  <footer class="slide-footer">
    <div class="footer-band"></div>
    <div class="brand"><span class="brand-square"></span><span class="brand-name">TJMalverne Consulting</span></div>
  </footer>
</section>

</body>
</html>
```